Webdesign für Brenner Flusskraft
Zielgruppe
Ansprechpartner für Planung und Errichtung von Stromerzeugung durch erneuerbare Energien. Alle Interessen im privaten, teilöffentlichen und öffentlichen Bereich, die mittel- und langfristig umweltschonenden Strom nutzen wollen.
Aufgabenstellung
- Farben bitte in den Unternehmensfarben Blau/Weiß mit einem kleinen Anteil Orange
- Bilder nach Möglichkeit bitte nur eigene (siehe Anhang)
- klare und übersichtliche Struktur
- KEIN Abklatsch der alten Webseite

```html
<!DOCTYPE html>
<html lang="de">
<head>
<meta charset="utf-8">
<title>Brenner Flusskraft</title>
<link href="https://fonts.googleapis.com/css2?family=Oswald:wght@400;500;600;700&family=Open+Sans:wght@400;600&family=Inter:wght@400;500&display=swap" rel="stylesheet">
<style>
:root{
  --navy:#262d66;
  --navy-deep:#1f2656;
  --ink:#141414;
  --text:#333;
  --band:#dcdfe7;
  --orange:#f28c00;
  --white:#fff;
}
*{margin:0;padding:0;box-sizing:border-box}
html,body{width:1200px;height:3177px;overflow:hidden;background:var(--white)}
body{position:relative;font-family:'Open Sans',sans-serif;color:var(--text)}
.abs{position:absolute}
h1,h2,h3,.btn,.nav a,.lead{font-family:'Oswald',sans-serif}
.btn{position:absolute;display:flex;align-items:center;justify-content:center;border-radius:22px;background:var(--navy);color:var(--white);font-size:17px;font-weight:500;text-decoration:none;height:44px}
.brand-name{font-family:'Oswald',sans-serif;font-weight:600;color:var(--navy);font-size:15px;display:flex;align-items:center;gap:6px;line-height:1.1}
.brand-dot{width:14px;height:14px;border-radius:50%;background:var(--navy);flex:none}
.brand-name.on-dark{color:var(--white);font-size:20px;gap:8px}
.brand-name.on-dark .brand-dot{background:var(--white);width:18px;height:18px}

/* hero */
.hero{left:0;top:0;width:1200px;height:676px;background:linear-gradient(100deg,#f1f3f6 0%,#e6eaef 38%,#b9c6d3 60%,#8fa2b3 80%,#6f8497 100%)}
.hero-photo{left:0;top:0;width:1200px;height:676px;background:linear-gradient(180deg,rgba(255,255,255,0) 0%,rgba(255,255,255,0) 30%,rgba(120,145,120,.25) 36%,rgba(255,255,255,0) 44%,rgba(160,175,190,.35) 100%)}
.hero-fade{left:0;top:0;width:700px;height:676px;background:linear-gradient(90deg,rgba(245,247,250,.85),rgba(245,247,250,0))}
.nav{left:559px;top:48px}
.nav a{position:absolute;white-space:nowrap;color:var(--ink);font-size:19px;text-decoration:none;top:0}
.hero h1{left:106px;top:178px;font-size:43px;line-height:56px;font-weight:700;color:var(--ink);letter-spacing:.5px}
.hero-text{left:106px;top:246px;width:500px;font-size:19px;line-height:26px;color:#222}
.badge{left:106px;top:465px;width:86px;height:86px;border-radius:50%;background:var(--white);border:6px solid #e0403a;box-shadow:0 1px 3px rgba(0,0,0,.2)}

/* about */
.about-photo{left:106px;top:746px;width:425px;height:524px;background:radial-gradient(ellipse at 50% 55%,#6a8fbf 0%,#3a5a48 40%,#1f3326 75%,#15241b 100%)}
.section-title{font-size:44px;font-weight:700;color:var(--ink);letter-spacing:.3px}
.lead{font-size:19px;font-weight:500;color:var(--ink);line-height:27px}
.body{font-size:17px;line-height:24px;color:#333}

/* partner */
.partner-band{left:0;top:1342px;width:1200px;height:389px;background:var(--band)}
.partner-mark{left:892px;top:1453px;width:204px;height:140px;display:flex;flex-direction:column;align-items:center;justify-content:center;gap:14px}
.partner-mark .square{width:80px;height:80px;background:#8a8aa6}
.partner-mark span{font-family:'Oswald',sans-serif;font-weight:600;font-size:36px;color:var(--navy)}
.orange-link{color:var(--orange);text-decoration:underline}

/* services */
.card{top:1883px;width:298px;height:423px;box-shadow:0 6px 12px rgba(38,45,102,.25);overflow:hidden}
.card-photo{inset:0;position:absolute}
.card-tint{inset:0;position:absolute;background:linear-gradient(180deg,rgba(38,45,102,.15) 0%,rgba(38,45,102,.55) 50%,rgba(38,45,102,.95) 72%,var(--navy) 100%)}
.card h3{position:absolute;left:15px;top:246px;font-size:32px;line-height:44px;font-weight:600;color:var(--white)}
.card p{position:absolute;left:15px;top:298px;width:278px;font-family:'Inter',sans-serif;font-size:16px;line-height:26.5px;color:var(--white);letter-spacing:-.5px}

/* career */
.career{left:0;top:2378px;width:1200px;height:459px;background:linear-gradient(90deg,#3c4256 0%,#2c3350 35%,#262c4a 60%,#283a32 100%)}
.career-title{left:530px;top:2448px;font-size:44px;line-height:53px;font-weight:600;color:var(--white)}
.career-lead{color:var(--white)}
.career-body{color:var(--white);font-family:'Inter',sans-serif;letter-spacing:-.4px;line-height:27px}

/* footer */
.footer{left:0;top:2837px;width:1200px;height:315px;background:var(--navy)}
.f-label{font-family:'Oswald',sans-serif;font-weight:500;font-size:17px;color:var(--white)}
.f-val{font-family:'Inter',sans-serif;font-size:15px;color:var(--white);letter-spacing:-.4px}
.f-link{font-family:'Oswald',sans-serif;font-weight:500;font-size:18px;color:var(--white);text-decoration:none}
.bottom-bar{left:0;top:3152px;width:1200px;height:25px;background:var(--navy-deep);display:flex;align-items:center;justify-content:center;font-family:'Inter',sans-serif;font-size:11px;color:var(--white);letter-spacing:-.3px}
</style>
</head>
<body>

<header class="hero abs">
  <div class="hero-photo abs" role="img" aria-label="Foto: Monteure installieren Solarmodule auf einem Flachdach"></div>
  <div class="hero-fade abs"></div>
  <div class="brand-name abs" style="left:106px;top:52px"><span class="brand-dot"></span>Brenner<br>Flusskraft</div>
  <nav class="nav abs">
    <a href="#" style="left:0">Home</a>
    <a href="#" style="left:88px">Unternehmen</a>
    <a href="#" style="left:231px">Leistungen
      <svg width="14" height="10" viewBox="0 0 14 10" style="vertical-align:middle"><path d="M2 2l5 5 5-5" fill="none" stroke="#141414" stroke-width="2"/></svg></a>
    <a href="#" style="left:354px">Referenzen</a>
    <a href="#" style="left:481px">Kontakt</a>
  </nav>
  <h1 class="abs">BRENNER FLUSSKRAFT</h1>
  <p class="hero-text abs">Ihr Ansprechpartner für Planung und Errichtung von Stromerzeugung durch erneuerbare Energien.<br><br>Kontaktieren Sie uns jetzt und starten Sie Ihre Reise zu nachhaltiger Energie!</p>
  <a class="btn" href="#" style="left:106px;top:402px;width:255px">Jetzt Kontakt aufnehmen</a>
  <div class="badge abs"></div>
</header>

<section class="about">
  <div class="about-photo abs" role="img" aria-label="Foto: zwei Geschäftsführer in hellblauen Hemden vor Grün"></div>
  <h2 class="section-title abs" style="left:562px;top:772px">ÜBER DAS UNTERNEHMEN</h2>
  <p class="lead abs" style="left:562px;top:845px;width:540px">Mit über 30 Jahren Erfahrung in der Planung und Errichtung von erneuerbare Energien Anlagen sind wir Ihre Ansprechpartner wenn es um die Stromerzeugung und Sektor Kopplung geht.</p>
  <p class="body abs" style="left:562px;top:944px;width:540px">Durch unsere große Erfahrung im Bereich des Energiebaus und der erneuerbaren Energien haben Sie mit uns ein leistungsfähiges Unternehmen für Ihre Projekte an der Hand. Sprechen Sie uns einfach für Ihre Projekte an, wir stehen von der Ingenieurplanung, über die Ausführung, bis hin zur Betriebsführung an Ihrer Seite.<br><br>Als Familienunternehmen in zweiter Generation finden Sie bei uns kurze Wege, hohe qualitative Leistungen und einen großenErfahrungsschatz.</p>
  <a class="btn" href="#" style="left:562px;top:1205px;width:307px">Mehr über unser Unternehmen</a>
</section>

<section>
  <div class="partner-band abs"></div>
  <h2 class="section-title abs" style="left:106px;top:1413px">UNSER PREMIUMPARTNER</h2>
  <p class="lead abs" style="left:106px;top:1486px;width:720px">Unsere exklusive Partnerschaft mit <span class="orange-link">Solveta</span>, einem führenden Unternehmen im Bereich Photovoltaik, ermöglicht es uns, erstklassige Energietechnik-Lösungen anzubieten.</p>
  <p class="body abs" style="left:106px;top:1553px;width:720px">Solveta steht für innovative, nachhaltige und effiziente Photovoltaik-Technologie, die unsere Mission zur Förderung erneuerbarer Energien unterstützt. Als Premiumpartner teilen wir die Vision einer sauberen und nachhaltigen Zukunft, in der erneuerbare Energiequellen eine zentrale Rolle spielen.</p>
  <div class="partner-mark abs"><div class="square"></div><span>Solveta</span></div>
</section>

<section>
  <h2 class="section-title abs" style="left:106px;top:1805px">UNSERE LEISTUNGEN</h2>
  <article class="card abs" style="left:106px">
    <div class="card-photo" role="img" aria-label="Foto: Wehr an einem Fluss mit Bäumen" style="background:linear-gradient(180deg,#8b947f,#4e5a46)"></div>
    <div class="card-tint"></div>
    <h3>WASSERKRAFT</h3>
    <p>Seit 25 Jahren sind wir Ihr kompetenter Ansprechpartner in Sachen Planung, Errichtung und Betrieb von Wasserkraftanlagen.</p>
  </article>
  <article class="card abs" style="left:451px">
    <div class="card-photo" role="img" aria-label="Foto: Solarfeld unter bewölktem Himmel" style="background:linear-gradient(180deg,#a9bccd,#6f8295)"></div>
    <div class="card-tint"></div>
    <h3>PHOTOVOLTAIK</h3>
    <p>Als Experten im Bereich regenerative Energien finden Sie mit uns Ihren Partner zur Verwirklichung Ihrer Photovoltaikprojekte.</p>
  </article>
  <article class="card abs" style="left:796px">
    <div class="card-photo" role="img" aria-label="Foto: Ladesäule für Elektrofahrzeuge" style="background:linear-gradient(180deg,#b3b7bd,#7a7f88)"></div>
    <div class="card-tint"></div>
    <h3>E-MOBILITÄT</h3>
    <p>Wir bieten Ihnen Testfahrten in Elektrofahrzeugen, Langzeitmieten und die Errichtung von Elektroladeparkplätzen an.</p>
  </article>
</section>

<section>
  <div class="career abs" role="img" aria-label="Foto: zwei Mitarbeiter sitzen vor einer Wand, dunkelblau getönt"></div>
  <h2 class="career-title abs">KARRIERE BEI<br>BRENNER FLUSSKRAFT</h2>
  <p class="lead career-lead abs" style="left:530px;top:2578px;width:560px">Schließen Sie sich unserem Team an und gestalten Sie die Zukunft der umweltschonenden Stromerzeugung.</p>
  <p class="body career-body abs" style="left:530px;top:2645px;width:530px">Bei Brenner Flusskraft finden Sie vielfältige Möglichkeiten, Ihre Leidenschaft für erneuerbare Energien in die Tat umzusetzen.</p>
  <a class="btn" href="#" style="left:530px;top:2725px;width:272px;background:#fff;color:var(--navy)">Zu den Stellenangeboten</a>
</section>

<footer>
  <div class="footer abs"></div>
  <div class="brand-name on-dark abs" style="left:205px;top:2976px"><span class="brand-dot"></span>Brenner<br>Flusskraft</div>
  <div class="abs" style="left:487px;top:2910px">
    <div class="f-label">Adresse</div>
    <div class="f-val">Uferweg 14, 09300 Talhain</div>
    <div class="f-label" style="margin-top:14px">Öffnugszeiten</div>
    <div class="f-val">Montag - Freitag 7:00 - 18:00 Uhr</div>
    <div class="f-label" style="margin-top:14px">Telefon</div>
    <div class="f-val">03700 / 4821</div>
  </div>
  <a class="f-link abs" href="#" style="left:890px;top:2918px">Kontakt</a>
  <a class="f-link abs" href="#" style="left:890px;top:2962px">Karriere</a>
  <a class="f-link abs" href="#" style="left:890px;top:3006px">Impressum</a>
  <a class="f-link abs" href="#" style="left:890px;top:3050px">Datenschutz</a>
  <div class="bottom-bar abs">© 2023 - Brenner Flusskraft Talhain| All rights reserved</div>
</footer>

</body>
</html>
```